Business cards to launch an education platform

Hi,
I am looking at having new business cards designed.
I am a startup, developing a web platform for schools and university, the education world. It's an online assessment system.
I would like a card that looks classy, and that is using the colors and the font of my logo.

I have attached:
1) my logo
2) A business card that I have designed quickly so you can have all the information required in the card, but I really don't like it.
3) The font that I am using (Lato Regular) to design my web platform
4) Some screenshots of my web platform so you can have a look at the style that I have.

Target Market(s)

Major market: Education system: Schools and university
Minor markets: Business in general

Industry/Entity Type

Business

Contact Information for Business Card

Clara Fenwick
Director

M: 0437 518 902
E: clara.fenwick@amberLoomSystems.com.au

Requirements
Must have
• The colors of my logo

```html
<!DOCTYPE html>
<html lang="en">
<head>
<meta charset="utf-8">
<title>Amber Loom Systems — Business Cards</title>
<link rel="stylesheet" href="https://fonts.googleapis.com/css2?family=Lato:wght@300;400;700&display=swap">
<style>
  :root {
    --navy: #1f4f9e;
    --cyan: #27b5e2;
    --ink: #2a3a5c;
    --card-top: #ffffff;
    --card-bottom: #eceef0;
    --backdrop: #dfe2e6;
  }
  * { margin: 0; padding: 0; box-sizing: border-box; }
  html, body {
    width: 1200px; height: 780px; overflow: hidden;
    background: var(--backdrop);
    font-family: "Lato", Arial, sans-serif;
  }
  .stage {
    position: relative; width: 1200px; height: 780px;
    display: flex; align-items: center; justify-content: center; gap: 60px;
  }
  .card {
    position: relative; width: 510px; height: 300px;
    border-radius: 22px;
    background: linear-gradient(160deg, var(--card-top) 0%, var(--card-bottom) 100%);
    box-shadow: 0 2px 0 #d3d6da, 0 4px 0 #c9ccd0, 0 14px 30px rgba(0,0,0,.18);
    overflow: hidden;
  }

  /* Front */
  .brand {
    position: absolute; left: 40px; top: 108px;
    display: flex; align-items: center; gap: 14px;
  }
  .brand-square { width: 34px; height: 34px; background: var(--navy); }
  .brand-name {
    color: var(--navy); font-weight: 400; font-size: 27px;
    letter-spacing: 1.5px; line-height: 1;
  }
  .holder {
    position: absolute; right: 40px; top: 36px; text-align: right;
  }
  .holder-name { color: var(--navy); font-size: 21px; font-weight: 400; }
  .holder-role { color: var(--cyan); font-size: 13px; font-weight: 300; letter-spacing: .5px; }
  .divider {
    position: absolute; left: 40px; right: 40px; top: 196px;
    height: 1.5px; background: var(--cyan);
  }
  .contact {
    position: absolute; left: 40px; top: 218px;
    list-style: none; color: var(--ink); font-size: 13px; line-height: 22px;
  }
  .contact li { display: flex; align-items: center; gap: 8px; }
  .contact svg { width: 14px; height: 14px; flex: none; }

  /* Back */
  .card-back .brand-back {
    position: absolute; inset: 0;
    display: flex; align-items: center; justify-content: center; gap: 16px;
  }
  .card-back .brand-square { width: 44px; height: 44px; }
  .card-back .brand-name { font-size: 32px; letter-spacing: 2px; }
</style>
</head>
<body>
<main class="stage">

  <section class="card card-front" aria-label="Business card front">
    <div class="brand">
      <span class="brand-square"></span>
      <span class="brand-name">Amber Loom Systems</span>
    </div>

    <div class="holder">
      <div class="holder-name">Clara Fenwick</div>
      <div class="holder-role">Director</div>
    </div>

    <div class="divider"></div>

    <ul class="contact">
      <li>
        <svg viewBox="0 0 14 14" aria-hidden="true">
          <rect width="14" height="14" rx="2" fill="var(--cyan)"/>
          <rect x="4.5" y="2.5" width="5" height="9" rx="1" fill="none" stroke="#fff" stroke-width="1.2"/>
        </svg>
        <span>0437 518 902</span>
      </li>
      <li>
        <svg viewBox="0 0 14 14" aria-hidden="true">
          <rect width="14" height="14" rx="2" fill="var(--cyan)"/>
          <rect x="2.5" y="4" width="9" height="6" fill="none" stroke="#fff" stroke-width="1.1"/>
          <path d="M2.5 4 L7 7.5 L11.5 4" fill="none" stroke="#fff" stroke-width="1.1"/>
        </svg>
        <span>clara.fenwick@amberLoomSystems.com.au</span>
      </li>
    </ul>
  </section>

  <section class="card card-back" aria-label="Business card back">
    <div class="brand-back">
      <span class="brand-square"></span>
      <span class="brand-name">Amber Loom Systems</span>
    </div>
  </section>

</main>
</body>
</html>
```